Local Flower Farm Needs Business Card Design

I need business cards designed for a flower farm based in Eudora, Kansas.
Business Info:
We are a local cut flower farm located in Eudora, Kansas, founded by Corinne Haldwick. What started as a passion for agriculture and search for more joy in daily life has blossomed into a small business dedicated to providing the community with beautiful, fresh, and sustainable flowers. We specialize in local, seasonal blooms, ensuring that every petal reflects the care and dedication we pour into our craft. Our mission is to deliver the highest quality flowers directly to our customers through local farmers markets and to florists who share our commitment to sustainability. Join us in celebrating the beauty of nature, one bloom at a time!
Contact Details:
Corinne Haldwick
Owner
Phone 913-555-0147
Facebook: Rosalind Thorpe Gardens
Instagram: @RosalindThorpeGardens
Website: RosalindThorpeGardens.example
Target Market(s)
Wholesale to Florists and Direct to Consumer via Farmers Market
Industry/Entity Type
Florist, Farm
Contact Information for Business Card
Name, Contact Info, Logo
Look and feel
Each slider illustrates characteristics of the customer's brand and the style your logo design should communicate.

```html
<!DOCTYPE html>
<html lang="en">
<head>
<meta charset="utf-8">
<title>Rosalind Thorpe Gardens – Business Card</title>
<link href="https://fonts.googleapis.com/css2?family=Montserrat:wght@400;700&display=swap" rel="stylesheet">
<style>
  :root {
    --backdrop: #e6e7e6;
    --ink: #0b2a2e;
    --paper: #ffffff;
    --text: #1b1b1b;
    --muted: #3a3a3a;
    --faint: #e4e4e4;
    --emboss: #1d4a4f;
  }
  * { box-sizing: border-box; margin: 0; padding: 0; }
  html, body { width: 1200px; height: 1108px; overflow: hidden; }
  body {
    background: var(--backdrop);
    font-family: "Montserrat", sans-serif;
    position: relative;
  }
  .card { position: absolute; overflow: hidden; }
  .card-front { left: 222px; top: 52px; width: 787px; height: 479px; background: var(--paper); }
  .card-back { left: 220px; top: 577px; width: 789px; height: 463px; background: var(--ink); }

  .header-band { position: absolute; left: 0; top: 40px; width: 100%; height: 86px; background: var(--ink); }
  .seal {
    position: absolute; left: 82px; top: 17px; width: 126px; height: 126px;
    border-radius: 50%; background: var(--paper); border: 2px solid var(--paper);
    box-shadow: inset 0 0 0 5px var(--paper), inset 0 0 0 6px var(--ink);
    display: flex; align-items: center; justify-content: center; text-align: center;
    color: var(--ink); font-weight: 700; font-size: 13px; line-height: 1.25; padding: 0 18px;
  }
  .holder { position: absolute; right: 52px; top: 50px; text-align: right; color: var(--paper); }
  .holder-name { font-weight: 700; font-size: 29px; letter-spacing: 0.2px; line-height: 1.1; }
  .holder-role { font-weight: 400; font-size: 18px; margin-top: 4px; }

  .watermark {
    position: absolute; left: 512px; top: 215px; width: 225px;
    color: var(--faint); font-weight: 700; font-size: 40px; line-height: 1.05; text-align: center;
  }

  .contact-list { position: absolute; left: 41px; top: 333px; list-style: none; }
  .contact-list li {
    display: flex; align-items: center; height: 28.5px;
    font-size: 18px; color: var(--text);
  }
  .contact-list svg { width: 17px; height: 17px; margin-right: 9px; flex: none; }

  .address { position: absolute; left: 534px; top: 399px; font-size: 18px; line-height: 22px; color: var(--text); }

  .emblem {
    position: absolute; left: 215px; top: 70px; width: 335px; height: 335px;
    border-radius: 50%; border: 2px solid var(--emboss);
    display: flex; align-items: center; justify-content: center; text-align: center;
    color: var(--emboss); font-weight: 700; font-size: 42px; line-height: 1.15; padding: 0 40px;
  }
</style>
</head>
<body>
  <section class="card card-front">
    <div class="header-band"></div>
    <div class="seal">Rosalind Thorpe Gardens</div>
    <div class="holder">
      <div class="holder-name">Corinne Haldwick</div>
      <div class="holder-role">Owner</div>
    </div>

    <div class="watermark">Rosalind Thorpe Gardens</div>

    <ul class="contact-list">
      <li>
        <svg viewBox="0 0 24 24" aria-hidden="true"><path fill="#1b1b1b" d="M6.6 10.8a15 15 0 0 0 6.6 6.6l2.2-2.2a1 1 0 0 1 1-.25 11.4 11.4 0 0 0 3.6.57 1 1 0 0 1 1 1V20a1 1 0 0 1-1 1A17 17 0 0 1 3 4a1 1 0 0 1 1-1h3.5a1 1 0 0 1 1 1c0 1.25.2 2.45.57 3.57a1 1 0 0 1-.25 1z"/></svg>
        913-555-0147
      </li>
      <li>
        <svg viewBox="0 0 24 24" aria-hidden="true"><circle cx="12" cy="12" r="10" fill="#1b1b1b"/></svg>
        Rosalind Thorpe Gardens
      </li>
      <li>
        <svg viewBox="0 0 24 24" aria-hidden="true"><circle cx="12" cy="12" r="10" fill="#1b1b1b"/></svg>
        @RosalindThorpeGardens
      </li>
      <li>
        <svg viewBox="0 0 24 24" aria-hidden="true"><g fill="none" stroke="#1b1b1b" stroke-width="2"><circle cx="12" cy="12" r="9.5"/><ellipse cx="12" cy="12" rx="4" ry="9.5"/><path d="M2.5 12h19"/></g></svg>
        www.RosalindThorpeGardens.example
      </li>
    </ul>

    <div class="address">418 Meadowlark Ln, #12<br>Eudora, KS 66025</div>
  </section>

  <section class="card card-back">
    <div class="emblem">Rosalind Thorpe Gardens</div>
  </section>
</body>
</html>
```